Business card for Sports Apparel business

DOUBLE SIDED DESIGN
We need business cards for a new sports apparel business. We are developing a protective headband for soccer initially.
Torvalle is focused on designing and developing head protection products to reduce the likelihood of concussion when playing sports. Exploring and understanding medical insights, material science research, current and former players experiences and governing bodies guidelines has allowed Torvalle to develop the safety, style, form and function requirements of a suitable product to bring to market.
Target Market(s)
Mums buying kits for the sons and daughters. Amateur footballers.
Industry/Entity Type
Sporting Good
Contact Information for Business Card
Martin Ashworth - CEO
Mobile: +44 7431589027
Email: martin@torvalle.co.uk
Tel: 0208 5519372
Helena Pargeter - COO
Mob: +44 7385 640117
Email: helena@torvalle.co.uk
Tel: 0208 5519372
Duncan Farrow - CCO
Mob: +44 7564 293081
Email: duncan@torvalle.co.uk
Tel: 0208 5519372
Look and feel
Each slider illustrates characteristics of the customer's brand and the style your logo design should communicate.

```html
<!DOCTYPE html>
<html lang="en">
<head>
<meta charset="utf-8">
<title>Torvalle Business Card</title>
<link href="https://fonts.googleapis.com/css2?family=Montserrat:wght@400;600;700&display=swap" rel="stylesheet">
<style>
  :root {
    --backdrop: #1f1f1f;
    --card-grey: #666666;
    --brand-blue: #125e95;
    --ink-white: #ffffff;
    --ink-soft: #e6e6e6;
  }
  * { margin: 0; padding: 0; box-sizing: border-box; }
  html, body {
    width: 1200px; height: 900px; overflow: hidden;
    background: var(--backdrop);
    font-family: "Montserrat", sans-serif;
  }
  .stage {
    position: relative; width: 1200px; height: 900px;
    display: flex; flex-direction: column; align-items: center; justify-content: center; gap: 50px;
  }
  .card {
    position: relative; width: 630px; height: 360px;
    background: var(--card-grey);
    box-shadow: 0 10px 30px rgba(0,0,0,0.5);
  }
  .card-front { display: flex; align-items: center; justify-content: center; }
  .wordmark {
    color: var(--ink-white); font-weight: 600; text-transform: uppercase;
    letter-spacing: 0.04em; line-height: 1;
  }
  .card-front .wordmark { font-size: 62px; }
  .card-back { background: var(--brand-blue); padding: 36px 40px; }
  .card-back-panel {
    width: 100%; height: 100%; background: var(--card-grey);
    display: flex; align-items: center; padding: 0 28px;
  }
  .card-back .wordmark { font-size: 32px; flex: 0 0 auto; }
  .divider {
    width: 1.5px; height: 150px; background: var(--ink-soft);
    margin: 0 22px 0 26px; flex: 0 0 auto;
  }
  .contact { color: var(--ink-white); }
  .contact-name {
    font-weight: 700; font-size: 17px; text-transform: uppercase; letter-spacing: 0.06em;
  }
  .contact-role { font-weight: 400; font-size: 14px; letter-spacing: 0.04em; margin-bottom: 18px; color: var(--ink-soft); }
  .contact-list { list-style: none; }
  .contact-list li {
    display: flex; align-items: center; gap: 10px;
    font-size: 15px; font-weight: 400; letter-spacing: 0.03em; line-height: 1.6;
  }
  .contact-list svg { width: 14px; height: 14px; flex: 0 0 auto; }
</style>
</head>
<body>
  <main class="stage">
    <section class="card card-front" aria-label="Card front">
      <span class="wordmark">Torvalle</span>
    </section>

    <section class="card card-back" aria-label="Card back">
      <div class="card-back-panel">
        <span class="wordmark">Torvalle</span>
        <span class="divider"></span>
        <div class="contact">
          <p class="contact-name">Martin Ashworth</p>
          <p class="contact-role">CEO</p>
          <ul class="contact-list">
            <li>
              <svg viewBox="0 0 14 14" fill="none" stroke="#fff" stroke-width="1.2"><rect x="4" y="1" width="6" height="12" rx="1"/><line x1="6" y1="11" x2="8" y2="11"/></svg>
              0208 551 9372
            </li>
            <li>
              <svg viewBox="0 0 14 14" fill="none" stroke="#fff" stroke-width="1.2"><path d="M3 1.5l2 0 1 3-1.5 1a7 7 0 0 0 4 4l1-1.5 3 1 0 2a1.5 1.5 0 0 1-1.5 1.5A10.5 10.5 0 0 1 1.5 3 1.5 1.5 0 0 1 3 1.5z"/></svg>
              +44 7431589027
            </li>
            <li>
              <svg viewBox="0 0 14 14" fill="none" stroke="#fff" stroke-width="1.2"><rect x="1" y="3" width="12" height="8"/><polyline points="1,3 7,8 13,3"/></svg>
              martin@torvalle.co.uk
            </li>
          </ul>
        </div>
      </div>
    </section>
  </main>
</body>
</html>
```